Cobalt Ridge Electric Needs A Logo Design

We need a logo for my new company based out of Sacramento, Ca called Cobalt Ridge Electric. The name says it all, my electrical contracting business provides "Cobalt Ridge Professional Work" I'm open to any colors that pop and customers to say Wow. I would love to print my cards on metal.

Industry/Entity Type

Business

Contact Information for Business Card

The card needs to have as follows
Name of company: Cobalt Ridge Electric
My Name: Marco Delvane
Phone # 916-555-0173
CL# 2049381
Email: cobaltridgeelectric@mailnest.example
and a slogan that represent "COBALT RIDGE"

Requirements
Must have
• The card needs to have as follows
• Name of company: Cobalt Ridge Electric
• My Name : Marco Delvane
• Phone # 916-555-0173
• CL# 2049381
• Email: cobaltridgeelectric@mailnest.example
• and a slogan that represent "COBALT RIDGE"
Nice to have
• popping colors
• electrical Arcing

```html
<!DOCTYPE html>
<html lang="en">
<head>
<meta charset="utf-8">
<title>Cobalt Ridge Electric — Business Card</title>
<link rel="stylesheet" href="https://fonts.googleapis.com/css2?family=Montserrat:wght@400;700&display=swap">
<style>
  :root {
    --backdrop: #e7e4df;
    --card-black: #050505;
    --card-sheen: #1c1c1c;
    --ink-white: #f4f4f4;
    --ink-blue: #2f8fd0;
    --ink-grey: #b9b9b9;
    --rule: #8a8a8a;
  }
  * { margin: 0; padding: 0; box-sizing: border-box; }
  html, body {
    width: 1200px;
    height: 1022px;
    overflow: hidden;
    background: var(--backdrop);
    font-family: "Montserrat", Arial, sans-serif;
  }
  .stage {
    width: 1200px;
    height: 1022px;
    display: flex;
    align-items: center;
    justify-content: center;
  }
  .business-card {
    position: relative;
    width: 900px;
    height: 514px;
    border-radius: 6px;
    background: linear-gradient(160deg, var(--card-sheen) 0%, var(--card-black) 55%, var(--card-black) 100%);
    box-shadow: 0 18px 40px rgba(0,0,0,0.35);
    display: flex;
    align-items: center;
    overflow: hidden;
  }
  .brand-block {
    width: 380px;
    padding-left: 20px;
    display: flex;
    flex-direction: column;
    align-items: center;
    text-align: center;
  }
  .brand-name {
    color: var(--ink-grey);
    font-weight: 700;
    font-size: 34px;
    letter-spacing: 2px;
    line-height: 1.1;
  }
  .slogan {
    color: var(--ink-grey);
    font-weight: 400;
    font-size: 14px;
    letter-spacing: 0.5px;
    margin-top: 12px;
  }
  .divider {
    width: 2px;
    height: 200px;
    background: var(--rule);
    flex: none;
  }
  .details {
    padding-left: 56px;
  }
  .company {
    color: var(--ink-white);
    font-weight: 700;
    font-size: 30px;
    letter-spacing: 0.5px;
    text-transform: uppercase;
  }
  .person {
    color: var(--ink-blue);
    font-weight: 700;
    font-size: 30px;
    letter-spacing: 1px;
    text-transform: uppercase;
    margin-top: 6px;
  }
  .contact-list {
    list-style: none;
    margin-top: 14px;
  }
  .contact-list li {
    color: var(--ink-white);
    font-size: 19px;
    display: flex;
    align-items: center;
    gap: 12px;
    line-height: 1.45;
  }
  .contact-list svg {
    width: 16px;
    height: 16px;
    flex: none;
  }
</style>
</head>
<body>
<main class="stage">
  <section class="business-card" aria-label="Cobalt Ridge Electric business card">
    <div class="brand-block">
      <span class="brand-name">COBALT RIDGE</span>
      <span class="slogan">Cobalt Ridge Professional Work</span>
    </div>
    <span class="divider" aria-hidden="true"></span>
    <div class="details">
      <h1 class="company">Cobalt Ridge Electric</h1>
      <h2 class="person">Marco Delvane</h2>
      <ul class="contact-list">
        <li>
          <svg viewBox="0 0 16 16" aria-hidden="true"><rect x="2" y="2" width="12" height="12" rx="1.5" fill="none" stroke="var(--ink-blue)" stroke-width="2"/></svg>
          2049381
        </li>
        <li>
          <svg viewBox="0 0 16 16" aria-hidden="true"><path d="M3 2 L6 2 L7 5 L5.5 6.5 Q7 9.5 9.5 10.5 L11 9 L14 10 L14 13 Q8 14 4 9 Q2 6 3 2 Z" fill="var(--ink-blue)"/></svg>
          916-555-0173
        </li>
        <li>
          <svg viewBox="0 0 16 16" aria-hidden="true"><rect x="2" y="2" width="12" height="12" rx="1.5" fill="none" stroke="var(--ink-blue)" stroke-width="2"/><path d="M4.5 8 L7 10.5 L11.5 5" fill="none" stroke="var(--ink-blue)" stroke-width="2"/></svg>
          cobaltridgeelectric@mailnest.example
        </li>
      </ul>
    </div>
  </section>
</main>
</body>
</html>
```